Business Card for Lantern Reach

Please design a Modern Business card for a Online Marketing Company

Website: http://www.lanternreach-example.com.au

Please do NOT include physical address in design.

```html
<!DOCTYPE html>
<html lang="en">
<head>
<meta charset="utf-8">
<title>Lantern Reach – Business Card</title>
<link rel="stylesheet" href="https://fonts.googleapis.com/css2?family=Roboto:wght@400;700;900&family=Open+Sans:wght@400;600&display=swap">
<style>
  :root {
    --bg: #e9e6e2;
    --charcoal: #232628;
    --crimson: #9b1b22;
    --amber: #e8731c;
    --orange: #fb4200;
    --white: #ffffff;
    --paper: #ffffff;
    --shadow: rgba(0,0,0,.28);
  }
  * { margin: 0; padding: 0; box-sizing: border-box; }
  html, body { width: 1200px; height: 483px; overflow: hidden; background: var(--bg); }
  .canvas {
    position: relative; width: 1200px; height: 483px;
    display: flex; align-items: center; justify-content: center; gap: 60px;
  }
  .card {
    position: relative; width: 520px; height: 296px; overflow: hidden;
    box-shadow: 0 10px 24px var(--shadow);
  }

  /* front */
  .card-front { background: var(--paper); }
  .front-header {
    height: 58px; background: var(--charcoal);
    display: flex; align-items: center; justify-content: center;
    font-family: "Roboto", sans-serif; font-size: 17px;
  }
  .front-header .person { color: var(--crimson); font-weight: 700; }
  .front-header .role { color: var(--amber); font-weight: 400; margin-left: 5px; }
  .brand {
    position: absolute; left: 0; right: 0; top: 102px;
    text-align: center; font-family: "Roboto", sans-serif;
  }
  .brand-name {
    color: var(--crimson); font-weight: 900; font-size: 28px;
    text-transform: uppercase; letter-spacing: -.3px; line-height: 1;
  }
  .brand-tagline {
    color: var(--charcoal); font-weight: 700; font-size: 13.5px; margin-top: 5px;
  }
  .divider {
    position: absolute; left: 0; right: 0; top: 185px; height: 4px;
    border-top: 1px solid var(--crimson); border-bottom: 1px solid var(--crimson);
  }
  .front-footer {
    position: absolute; left: 0; right: 0; top: 193px; bottom: 0;
    background: var(--orange);
    display: flex; flex-direction: column; align-items: center; justify-content: center; gap: 9px;
    font-family: "Open Sans", sans-serif; font-size: 13.5px; color: var(--white);
  }
  .contact { display: flex; align-items: center; gap: 7px; }
  .contact svg { width: 13px; height: 13px; }

  /* back */
  .card-back {
    background: var(--orange); color: var(--white);
    font-family: "Roboto", sans-serif;
  }
  .back-brand { position: absolute; left: 60px; top: 92px; }
  .back-name {
    font-weight: 900; font-size: 40px; text-transform: uppercase; line-height: 1; letter-spacing: -.3px;
  }
  .back-tagline { font-weight: 700; font-size: 19px; margin: 6px 0 0 90px; }
  .back-web {
    position: absolute; left: 0; right: 0; bottom: 46px; text-align: center;
    font-family: "Open Sans", sans-serif; font-size: 17px; letter-spacing: .5px;
  }
</style>
</head>
<body>
<main class="canvas">
  <section class="card card-front" aria-label="Card front">
    <header class="front-header">
      <span class="person">Your Name,</span><span class="role">Title</span>
    </header>
    <div class="brand">
      <div class="brand-name">Lantern Reach</div>
      <div class="brand-tagline">Be found online - Grow online</div>
    </div>
    <div class="divider"></div>
    <footer class="front-footer">
      <div class="contact">
        <svg viewBox="0 0 16 16" aria-hidden="true"><circle cx="8" cy="8" r="7.5" fill="#fff"/><path d="M5.5 4.5l1.5 1.8-.8 1c.6 1.2 1.3 1.9 2.5 2.5l1-.8 1.8 1.5-.9 1.2c-2.8-.5-5.2-2.9-5.8-5.8z" fill="var(--orange)"/></svg>
        <span>0491 570 156</span>
      </div>
      <div class="contact">
        <svg viewBox="0 0 16 16" aria-hidden="true"><circle cx="8" cy="8" r="7.5" fill="#fff"/><rect x="4" y="5" width="8" height="6" fill="var(--orange)"/><path d="M4 5l4 3.2L12 5" stroke="#fff" stroke-width="1" fill="none"/></svg>
        <span>hello@lanternreach-example.com.au</span>
      </div>
      <div class="contact">
        <svg viewBox="0 0 16 16" aria-hidden="true"><circle cx="8" cy="8" r="7.5" fill="#fff"/><g stroke="var(--orange)" stroke-width="1" fill="none"><circle cx="8" cy="8" r="4.5"/><ellipse cx="8" cy="8" rx="2" ry="4.5"/><path d="M3.5 8h9"/></g></svg>
        <span>www.lanternreach-example.com.au</span>
      </div>
    </footer>
  </section>

  <section class="card card-back" aria-label="Card back">
    <div class="back-brand">
      <div class="back-name">Lantern Reach</div>
      <div class="back-tagline">Be found online - Grow online</div>
    </div>
    <div class="back-web">www.lanternreach-example.com.au</div>
  </section>
</main>
</body>
</html>
```